Website design for Puddle Jump Kidscare

I need a website designed for my daycare business, Puddle Jump Kidscare, now that I have a new logo. My former website was ok but simple and I did not have a logo yet. It also was created by me using a template and was entirely pink. I loved the bright, happy feel of it but worried it might not appeal as much to potential clients who have sons. Therefore, I need a site which will appeal to both genders while still keeping the cheerful color scheme of my new logo, which has pinks, blue, green and cream.
Updates

Reason: Hello! I am still trying to download my new logo and am sorry it is taking me so long. Hopefully I will it posted by the end of today (US Eastern Standard Time). Thank you all very much for your patience!

Hello! I have finally managed to upload my new logo for you to use in designing my website. I'm sorry it took so long and greatly appreciate your time and creative efforts! I look forward to seeing what is submitted based on my logo design and its style/colors.

Many thanks!

Reason: As I've been traveling and posted my logo file late, I am extending my deadline. I am now back and can focus on providing more and better feedback. I appreciate your patience and submissions very much!

Reason: I need more time to provide feedback and make decisions.

Industry/Entity Type

Daycare

Colors
0192cd
33a6d7
86cae7
cadf82
fbf289
add136
e34197

```html
<!DOCTYPE html>
<html lang="en">
<head>
<meta charset="utf-8">
<title>Puddle Jump Kidscare</title>
<link href="https://fonts.googleapis.com/css2?family=Open+Sans:wght@400;600;700&family=Schoolbell&display=swap" rel="stylesheet">
<style>
:root{
  --header-grey:#4a4a4a;
  --sky:#33a6d7;
  --ocean:#0192cd;
  --sun:#f0e384;
  --leaf:#a2c22a;
  --pink:#e34197;
  --ink:#3a3a3a;
  --white:#ffffff;
  --card-shadow:#cfc463;
}
*{margin:0;padding:0;box-sizing:border-box}
html,body{width:904px;height:1200px;overflow:hidden}
body{position:relative;font-family:"Open Sans",Arial,sans-serif;color:var(--ink);background:var(--white)}
.abs{position:absolute}

.site-header{left:0;top:0;width:904px;height:95px;background:var(--header-grey)}
.brand{left:60px;top:22px;display:flex;align-items:center;gap:12px}
.brand-name{color:var(--white);font-size:20px;font-weight:600;line-height:25px;width:130px}
.brand-dot{width:46px;height:46px;border-radius:50%;background:#6a6a6a}

.main-nav{left:0;top:95px;width:904px;height:34px;background:var(--sky);display:flex;align-items:center;padding-left:59px;gap:21px}
.main-nav a{color:var(--white);text-decoration:none;font-weight:700;font-size:12px;letter-spacing:.5px}

.hero{left:0;top:129px;width:904px;height:145px;background:linear-gradient(90deg,#b44c86 0%,#d977b3 30%,#e08ac0 55%,#d27aad 80%,#a94a80 100%)}
.hero-title{left:0;top:172px;width:904px;text-align:center;color:var(--white);font-weight:700;font-size:19px;line-height:23px;letter-spacing:1.2px}
.hero-rule{left:0;top:274px;width:904px;height:5px;background:var(--sky)}

.intro{left:0;top:279px;width:904px;height:321px;background:var(--sun)}
.card{background:var(--white);border-radius:10px;box-shadow:3px 3px 0 var(--card-shadow)}
.card h2{font-family:"Schoolbell","Comic Sans MS",cursive;font-weight:400;color:var(--pink);font-size:34px;line-height:40px}
.greeting{left:52px;top:308px;width:388px;height:257px;padding:12px 20px 0 23px}
.greeting p{font-size:10.5px;line-height:15.4px;margin-top:6px}
.greeting p.lead{font-size:11.6px;line-height:17.6px;margin-top:12px}
.sign{text-align:right;margin-top:18px!important}
.news{left:603px;top:309px;width:249px;height:241px;padding:12px 22px 0 23px}
.news p{font-size:10.3px;line-height:15.3px;margin-top:9px}
.news p.lead{margin-top:14px}
.posted{text-align:right;margin-top:18px!important}

.portrait{left:464px;top:309px;width:114px;height:114px;border-radius:50%;background:radial-gradient(circle at 50% 45%,#b98d78 0%,#6b4a3c 55%,#2e2320 100%);box-shadow:2px 3px 0 var(--card-shadow)}
.mascot{left:472px;top:460px;width:104px;height:95px;border-radius:45% 45% 30% 30%;background:linear-gradient(180deg,#c9c43a 0%,#86b064 35%,#5f9448 100%)}

.benefits-band{left:0;top:600px;width:904px;height:65px;background:var(--sky);text-align:center;color:var(--white);font-weight:700;font-size:19px;letter-spacing:1.2px;line-height:65px}
.benefits{left:0;top:665px;width:904px;height:310px;background:var(--ocean)}
.benefit{top:693px;width:235px;color:var(--white)}
.benefit .photo{width:114px;height:114px;border-radius:50%;margin:0 auto;box-shadow:0 3px 0 #86cae7}
.benefit h3{font-family:"Schoolbell","Comic Sans MS",cursive;font-weight:400;font-size:28px;text-align:center;margin-top:10px;line-height:32px}
.benefit p{font-size:11.6px;line-height:17.6px;margin-top:9px}

.site-footer{left:0;top:975px;width:904px;height:225px;background:var(--leaf);border-top:1px solid #c5de78}
.fcol{top:20px;color:var(--white);font-size:11.5px;line-height:12.8px}
.fcol h4{font-size:11px;font-weight:700;letter-spacing:1px;margin-bottom:6px}
.fcol ul{list-style:none;line-height:14.4px}
.fcol li::before{content:"• ";font-size:9px}
.fdiv{top:20px;width:1px;height:135px;background:#c2dc6a}
.socials{display:flex;gap:7px;margin-top:7px}
.socials span{width:20px;height:20px;border-radius:3px;background:var(--white)}
.frule{left:57px;top:173px;width:798px;height:1px;background:#c2dc6a}
.copyright{left:58px;top:180px;color:var(--white);font-size:12px;letter-spacing:.5px}
</style>
</head>
<body>

<header class="site-header abs">
  <div class="brand abs"><span class="brand-name">Puddle Jump<br>Kidscare</span><span class="brand-dot"></span></div>
</header>

<nav class="main-nav abs">
  <a href="#">Home</a><a href="#">About Us</a><a href="#">Services</a><a href="#">Hours and Fees</a><a href="#">Policies</a><a href="#">Photo Gallery</a><a href="#">Testimonials</a><a href="#">Contact Us</a>
</nav>

<div class="hero abs" role="img" aria-label="Soft-focus photo of children playing with toys, tinted pink"></div>
<h1 class="hero-title abs">Welcome to Puddle Jump Kidscare, a playspace where<br>children can play, create, and imagine!</h1>
<div class="hero-rule abs"></div>

<section class="intro abs"></section>

<article class="card greeting abs">
  <h2>Greetings!</h2>
  <p class="lead">Welcome to Puddle Jump Kidscare, a licensed Group Family Day Care, located in New York City's beautiful Upper East Side. We are located on a pretty, tree-lined block on East 74th Street, between 1st and 2nd Avenues.</p>
  <p>We are a few blocks from the 6 line subway and the 79th Street bus route, and we offer flexible hourly childcare, making it as easy as possible for busy parents on the go to arrange their children's care.</p>
  <p>We invite you to learn more about us and hope you will visit us soon!</p>
  <p class="sign">— Marcus &amp; Helen Dorsey</p>
</article>
<svg class="abs" style="left:438px;top:398px" width="24" height="24" aria-hidden="true"><polygon points="0,2 22,2 2,20" fill="#fff"/><polyline points="22,2 2,20" stroke="#cfc463" stroke-width="3" fill="none"/></svg>

<div class="portrait abs" role="img" aria-label="Portrait photo of the daycare owner"></div>
<div class="mascot abs" role="img" aria-label="Illustration of a smiling green frog wearing a small crown"></div>

<article class="card news abs">
  <h2>Latest News</h2>
  <p class="lead">We are thrilled to have found a new cheerful space with a private backyard! It's large, sunny, and filled with outdoor play equipment such as a toddler slide, sand/water activity table, and lots of toys!</p>
  <p>Please stay tuned for updates on our program and services as we say goodbye to Winter and hello to Spring!</p>
  <p class="posted">— Posted: May-02-2014</p>
</article>
<svg class="abs" style="left:583px;top:468px" width="22" height="22" aria-hidden="true"><polygon points="22,0 22,20 2,20" fill="#fff"/><polyline points="2,20 22,20" stroke="#cfc463" stroke-width="3" fill="none"/></svg>

<div class="benefits-band abs">The benefits of choosing Puddle Jump Kidscare:</div>
<section class="benefits abs"></section>

<div class="benefit abs" style="left:60px">
  <div class="photo" role="img" aria-label="Photo of a smiling boy balancing an open book on his head" style="background:radial-gradient(circle at 50% 45%,#e8cdb4 0%,#bfc6cf 60%,#f2f2f2 100%)"></div>
  <h3>learning</h3>
  <p>We develop age-appropriate activities that introduce and strengthen academic and social skills.</p>
</div>
<div class="benefit abs" style="left:337px">
  <div class="photo" role="img" aria-label="Photo of open paint pots and brushes" style="background:linear-gradient(135deg,#d84a8f 0%,#2fa37a 35%,#e8c93a 55%,#d1303d 70%,#2447b8 100%)"></div>
  <h3>creativity</h3>
  <p>We offer children a wide range of creative opportunities including art projects, toddler yoga lessons, afternoon tea parties, dress up play, and a large selection of books and games.</p>
</div>
<div class="benefit abs" style="left:617px">
  <div class="photo" role="img" aria-label="Photo of two young girls sharing a lollipop" style="background:radial-gradient(circle at 50% 50%,#f1d2b8 0%,#e8c08a 55%,#f4f0e8 100%)"></div>
  <h3>sharing</h3>
  <p>We strive to include enrichment activities that extend your child's understanding of the world and their role in it.</p>
</div>

<footer class="site-footer abs">
  <div class="fcol abs" style="left:57px">
    <h4>PUDDLE JUMP KIDSCARE</h4>
    Marcus Dorsey<br>212 East 74th Street<br>New York, NY 10021<br><br>Phone: (917) 555-0142<br>Email: hi@puddlejump.com
  </div>
  <div class="fdiv abs" style="left:244px"></div>
  <div class="fcol abs" style="left:263px">
    <h4>PLAYCARE HOURS</h4>
    Monday - Friday<br>8:00AM to 6:00PM
  </div>
  <div class="fdiv abs" style="left:451px"></div>
  <div class="fcol abs" style="left:472px;top:18px">
    <h4>SITEMAP</h4>
    <ul><li>Home</li><li>About Us</li><li>Services</li><li>Hours &amp; Fees</li><li>Policies</li><li>Photo Gallery</li><li>Testimonials</li><li>Contact Us</li></ul>
  </div>
  <div class="fdiv abs" style="left:658px"></div>
  <div class="fcol abs" style="left:677px">
    <h4>SOCIAL NETWORKS</h4>
    <div class="socials"><span></span><span></span><span></span><span></span></div>
  </div>
  <div class="frule abs"></div>
  <p class="copyright abs">© Puddle Jump Kidscare, 2014 | Website by Brightleaf Studio</p>
</footer>

</body>
</html>
```